Wellness, Meaning, and the Inner Journey Research Program Website

Overview: This website will serve a new research program (Wellness, Meaning, and the Inner Journey) at the Harrowgate University School of Medicine. I want a clean, intuitive design that has a navigation bar, but uses icons/graphic buttons to link to the main pages. In an attached Word document, I have provided a basic information architecture for the site, understanding that this project would just generate graphics and code for the 3 pages. I highlighted the 3 pages I'd like designed.
Target market: People who want to participate in our research, or contribute grant funding to specific projects.
Number of page: The design project focuses on 3 pages, but the site must accommodate 6 pages with top-level links. See attached Word doc.
Logo and website header: Please integrate our logo in the header. I've uploaded it as a png file--both with the name of the website and with just the logo image. I imaging the logo would look great in a banner set against an image of a mountain. The two main design themes I want to see included are nature and healthcare.
Text content: I have not yet provided text. Use some dummy text.
Technical Specifications:
- Build using WordPress. We will host this site ourselves on NetHarbor using WordPress.
- The design package must be coded.
- The template must be responsive to different platforms (e.g., computer, mobile phone, iPad).
Thank you! I look forward to seeing your designs.
- Ned

```html
<!DOCTYPE html>
<html lang="en">
<head>
<meta charset="utf-8">
<title>Wellness, Meaning, and the Inner Journey – The Research Program</title>
<link rel="stylesheet" href="https://fonts.googleapis.com/css2?family=Montserrat:wght@700&family=Roboto:wght@400;500;700&display=swap">
<style>
:root{
  --blue:#175e9a;
  --blue-text:#1b5c95;
  --green:#7dab33;
  --teal:#1e6d5a;
  --teal-dark:#16574a;
  --ink:#2b2b2b;
  --body:#666;
  --grey-bg:#f3f3f3;
  --footer:#2a2a2a;
  --white:#fff;
}
*{box-sizing:border-box;margin:0;padding:0}
html,body{width:1200px;height:3805px;overflow:hidden}
body{font-family:"Roboto",Arial,sans-serif;color:var(--ink);background:var(--white)}
.page{position:relative;width:1200px;height:3805px;overflow:hidden}
.abs{position:absolute}
h1,h2{font-family:"Montserrat",Arial,sans-serif;font-weight:700;text-transform:uppercase}

/* header */
.header{top:0;left:0;width:1200px;height:96px;background:var(--white)}
.phone-badge{left:111px;top:13px;width:50px;height:50px;border-radius:50%;background:#fff;box-shadow:0 2px 6px rgba(0,0,0,.18);display:flex;align-items:center;justify-content:center}
.phone-number{left:184px;top:26px;font-size:18px;font-weight:500;color:var(--blue-text)}
.brand{display:flex;align-items:center;gap:10px}
.brand-mark{width:34px;height:34px;border-radius:50%;background:var(--green)}
.brand-name{font-family:"Roboto",sans-serif;font-weight:700;font-size:13px;line-height:16px;color:var(--blue-text)}
.header .brand{left:445px;top:16px}
.social{display:flex;gap:7px}
.social span{display:block;width:36px;height:36px;border-radius:50%}
.header .social{left:922px;top:19px}
.header .social span{border:2px solid var(--teal)}
.header .social span:first-child{background:var(--teal)}

.nav{left:111px;top:72px;width:978px;height:51px;background:var(--blue);display:flex;justify-content:center;align-items:center;gap:48px}
.nav a,.footer-nav a{color:#fff;text-decoration:none;font-weight:700;text-transform:uppercase}
.nav a{font-size:16px}

/* hero */
.hero{top:96px;left:0;width:1200px;height:690px;background:
  radial-gradient(ellipse at 70% 25%,rgba(255,240,200,.95) 0%,rgba(245,200,130,.6) 25%,rgba(0,0,0,0) 55%),
  linear-gradient(160deg,#6b5a44 0%,#a3763f 30%,#c98e45 55%,#7a4f28 80%,#3f2f22 100%)}
.hero-title{left:100px;top:214px;width:524px;text-align:center;color:#fff;font-size:34px;line-height:44px;letter-spacing:.5px;text-shadow:0 2px 6px rgba(0,0,0,.3)}
.btn{display:flex;align-items:center;gap:14px;height:52px;padding:0 22px 0 5px;border-radius:26px;background:var(--teal);color:#fff;font-weight:700;font-size:15px;text-transform:uppercase;text-decoration:none}
.btn-dot{width:42px;height:42px;border-radius:50%;background:#fff;flex:none}
.hero .btn{position:absolute;left:273px;top:333px}
.btn.green{background:#4a8a2f}

/* about */
.about{top:724px;left:0;width:1200px;height:525px;background:linear-gradient(180deg,#f3f3f3 0%,#eef0e6 55%,#e7eadb 100%)}
.about-mark{left:115px;top:95px;width:415px;height:385px;border-radius:50%;background:radial-gradient(circle,rgba(125,171,51,.35) 0%,rgba(23,94,154,.18) 60%,rgba(255,255,255,0) 72%)}
.about h2{left:600px;top:130px;font-size:36px;color:var(--ink)}
.copy{font-size:14.5px;line-height:26px;color:var(--body);text-align:justify}
.about .copy{left:600px;top:198px;width:489px}
.about .btn{position:absolute;left:600px;top:390px}

/* team */
.team{top:1249px;left:0;width:1200px;height:507px;background:#fff}
.team h2{left:0;top:92px;width:1200px;text-align:center;font-size:37px}
.member{top:180px;width:250px;text-align:center}
.avatar{width:130px;height:130px;margin:0 auto;border-radius:50%;border:5px solid #fff;box-shadow:0 0 0 2px #ddd,0 2px 8px rgba(0,0,0,.12);background:linear-gradient(180deg,#c9b49b,#6e7d5c)}
.member h3{margin-top:20px;font-size:20px;font-weight:500;color:var(--blue-text);text-transform:uppercase}
.member p{margin-top:10px;font-size:14px;line-height:22px;color:var(--body)}

/* projects */
.projects{top:1756px;left:0;width:1200px;height:581px;background:linear-gradient(180deg,#1f6e5b 0%,#1a6352 45%,#2d6d3d 100%)}
.projects h2{left:0;top:62px;width:1200px;text-align:center;font-size:37px;color:#fff}
.card{top:143px;width:314px;height:368px;background:#fff;border-radius:4px;padding:7px;text-align:center}
.card-img{height:190px}
.card h3{margin-top:20px;font-size:18px;font-weight:500;color:var(--blue-text);text-transform:uppercase}
.card p{margin:12px auto 0;width:270px;font-size:14px;line-height:24px;color:var(--body)}
.more{display:inline-flex;align-items:center;gap:8px;margin-top:9px;font-size:14px;font-weight:500;color:var(--teal);text-decoration:none}

/* focus */
.focus{top:2337px;left:0;width:1200px;height:471px;background:var(--grey-bg)}
.focus h2{left:111px;top:70px;font-size:37px}
.focus .copy{left:111px;top:142px;width:489px}
.focus .btn{position:absolute;left:111px;top:337px}
.venn{left:670px;top:30px;width:420px;height:420px}
.circle{position:absolute;border-radius:50%;color:#fff;text-align:center}
.circle h4{font-size:15px;font-weight:500;text-transform:uppercase}
.circle p{font-size:12px;line-height:17px;margin-top:6px}

/* faq */
.faq{top:2808px;left:0;width:1200px;height:500px;background:#fff}
.faq h2{left:0;top:84px;width:1200px;text-align:center;font-size:37px}
.faq-item{left:214px;width:772px;height:52px;border-radius:26px;background:#fff;box-shadow:0 1px 6px rgba(0,0,0,.15);display:flex;align-items:center;justify-content:space-between;padding:0 8px 0 25px;font-size:15px;color:#333}
.plus{width:40px;height:40px;border-radius:50%;background:var(--teal);display:flex;align-items:center;justify-content:center}

/* footer */
.footer-bg{top:3400px;left:0;width:1200px;height:405px;background:var(--footer)}
.footer .brand{left:400px;top:3515px}
.footer .brand-name{color:#fff;font-size:16px;line-height:19px}
.footer .brand-mark{width:40px;height:40px;background:#fff}
.footer-nav{left:0;top:3597px;width:1200px;display:flex;justify-content:center;gap:44px}
.footer-nav a{font-size:20px;font-weight:500}
.contact{left:0;top:3640px;width:1200px;display:flex;justify-content:center;align-items:center;gap:16px;color:#fff;font-size:20px;font-weight:500}
.contact span{display:flex;align-items:center;gap:10px}
.footer .social{left:515px;top:3692px}
.footer .social span{border:2px solid var(--teal)}
.footer .social span:first-child{background:var(--teal)}
.rule{left:125px;top:3754px;width:950px;height:1px;background:#444}
.copyright{left:0;top:3770px;width:1200px;text-align:center;color:#ddd;font-size:13px}
.copyright em{font-style:normal;color:var(--blue)}
</style>
</head>
<body>
<div class="page">

  <!-- hero -->
  <div class="abs hero" role="img" aria-label="Photo: person with arms outstretched on a sunlit mountain ridge">
    <h1 class="abs hero-title">Wellness, Meaning, and<br>the Inner Journey</h1>
    <a class="btn" href="#"><span class="btn-dot"></span>Get Started</a>
  </div>
  <svg class="abs" style="left:0;top:590px" width="1200" height="200" viewBox="0 590 1200 200" aria-hidden="true">
    <path d="M0 724 C150 650 270 600 430 622 C620 650 760 790 990 770 C1090 760 1160 720 1200 692 L1200 790 L0 790 Z" fill="#7dab33"/>
    <path d="M0 736 C150 672 270 636 430 654 C620 676 740 780 960 764 C1080 755 1160 735 1200 715 L1200 790 L0 790 Z" fill="#f3f3f3"/>
  </svg>

  <!-- header -->
  <header class="abs header">
    <div class="abs phone-badge">
      <svg width="24" height="24" viewBox="0 0 24 24"><path d="M6.6 10.8a15 15 0 0 0 6.6 6.6l2.2-2.2c.3-.3.7-.4 1-.2 1.1.4 2.3.6 3.6.6.6 0 1 .4 1 1V20c0 .6-.4 1-1 1A17 17 0 0 1 3 4c0-.6.4-1 1-1h3.5c.6 0 1 .4 1 1 0 1.3.2 2.5.6 3.6.1.3 0 .7-.2 1z" fill="#7dab33"/></svg>
    </div>
    <div class="abs phone-number">123-456-7890</div>
    <div class="abs brand"><span class="brand-mark"></span><span class="brand-name">Wellness, Meaning, and the Inner Journey<br>The Research Program</span></div>
    <div class="abs social" aria-label="Social links"><span></span><span></span><span></span><span></span></div>
  </header>
  <nav class="abs nav"><a href="#">Home</a><a href="#">People</a><a href="#">Projects</a><a href="#">FAQs</a><a href="#">Resources</a><a href="#">Contact</a></nav>

  <!-- about -->
  <section class="abs about">
    <div class="abs about-mark" role="img" aria-label="Large faint program emblem over a meadow landscape"></div>
    <h2 class="abs">About Us</h2>
    <p class="abs copy">Lorem ipsum dolor sit amet, consectetur adipiscing elit, sed do eiusmod tempor incididunt ut labore et dolore magna aliqua. Ut enim ad minim veniam, quis nostrud exercitationa.Labore et dolore magna aliqt enim ad minim veniam, quis nostrud exeenim ad minim veniam, quis nostrud exercitationarcitexercitationa. Labore et dolore magna aliqt enim ad minim veniam, quis nostrud ullamco nisi ut aliquipa.</p>
    <a class="btn" href="#"><span class="btn-dot"></span>Learn More</a>
  </section>

  <!-- team -->
  <section class="abs team">
    <h2 class="abs">Research Team</h2>
    <div class="abs member" style="left:100px"><div class="avatar" role="img" aria-label="Portrait of team member"></div><h3>John Smith</h3><p>Lorem ipsum dolor sit amet cons<br>ectum dolor ameetur.</p></div>
    <div class="abs member" style="left:350px"><div class="avatar" role="img" aria-label="Portrait of team member"></div><h3>John Smith</h3><p>Lorem ipsum dolor sit amet cons<br>ectum dolor ameetur.</p></div>
    <div class="abs member" style="left:600px"><div class="avatar" role="img" aria-label="Portrait of team member"></div><h3>John Smith</h3><p>Lorem ipsum dolor sit amet cons<br>ectum dolor ameetur.</p></div>
    <div class="abs member" style="left:850px"><div class="avatar" role="img" aria-label="Portrait of team member"></div><h3>John Smith</h3><p>Lorem ipsum dolor sit amet cons<br>ectum dolor ameetur.</p></div>
  </section>

  <!-- projects -->
  <section class="abs projects" role="img" aria-label="Misty green forested hills background">
    <h2 class="abs">Research Projects</h2>
    <article class="abs card" style="left:111px">
      <div class="card-img" role="img" aria-label="Photo: hiker facing alpine peaks" style="background:linear-gradient(180deg,#b9c7d2 0%,#8b8c82 45%,#6f7a3c 75%,#a77a35 100%)"></div>
      <h3>Lorem Ipsum Dolor</h3>
      <p>Sed ut perspiciatis unde omnis iste natus error sit voluptatem accusantium dol oremque laudantiuma.</p>
      <a class="more" href="#">Learn More <svg width="14" height="14" viewBox="0 0 14 14"><circle cx="7" cy="7" r="7" fill="#1e6d5a"/><path d="M5 4l3 3-3 3" stroke="#fff" stroke-width="1.8" fill="none"/></svg></a>
    </article>
    <article class="abs card" style="left:443px">
      <div class="card-img" role="img" aria-label="Photo: hikers walking through a sunlit forest" style="background:linear-gradient(135deg,#f3ead0 0%,#9a8a55 35%,#4c5a2c 70%,#2c3320 100%)"></div>
      <h3>Lorem Ipsum Dolor</h3>
      <p>Sed ut perspiciatis unde omnis iste natus error sit voluptatem accusantium dol oremque laudantiuma.</p>
      <a class="more" href="#">Learn More <svg width="14" height="14" viewBox="0 0 14 14"><circle cx="7" cy="7" r="7" fill="#1e6d5a"/><path d="M5 4l3 3-3 3" stroke="#fff" stroke-width="1.8" fill="none"/></svg></a>
    </article>
    <article class="abs card" style="left:774px">
      <div class="card-img" role="img" aria-label="Photo: hiker celebrating on a rocky summit above clouds" style="background:linear-gradient(180deg,#dfe6ea 0%,#b8c6cc 45%,#7f95a0 70%,#6c5d4f 100%)"></div>
      <h3>Lorem Ipsum Dolor</h3>
      <p>Sed ut perspiciatis unde omnis iste natus error sit voluptatem accusantium dol oremque laudantiuma.</p>
      <a class="more" href="#">Learn More <svg width="14" height="14" viewBox="0 0 14 14"><circle cx="7" cy="7" r="7" fill="#1e6d5a"/><path d="M5 4l3 3-3 3" stroke="#fff" stroke-width="1.8" fill="none"/></svg></a>
    </article>
  </section>

  <!-- focus -->
  <section class="abs focus">
    <h2 class="abs">Our Focus</h2>
    <p class="abs copy">Lorem ipsum dolor sit amet, consectetur adipiscing elit, sed do eiusmod tempor incididunt ut labore et dolore magna aliqua. Ut enim ad minim veniam, quis nostrud exercitationa.Labore et dolore magna aliqt enim ad minim veniam, quis nostrud exeenim ad minim veniam, quis nostrud exercitationarcitexercitationa. Labore et dolore magna aliqt enim ad minim veniam, quis nostrud ullamco nisi ut aliquipa.</p>
    <a class="btn" href="#"><span class="btn-dot"></span>Learn More</a>
    <div class="abs venn">
      <div class="circle" style="left:87px;top:0;width:246px;height:246px;background:#1f639f;padding-top:30px">
        <svg width="44" height="36" viewBox="0 0 44 36"><path d="M18 32 4 18A8 8 0 0 1 18 8a8 8 0 0 1 14 6" fill="#fff"/><circle cx="32" cy="24" r="9" fill="#fff"/><path d="M32 19v10M27 24h10" stroke="#1f639f" stroke-width="2.4"/></svg>
        <h4>Healthcare</h4>
        <p>Lorem ipsum dolor sit amet, con<br>sectetur adipiscing elit, sed do<br>eiusmod tempora.</p>
      </div>
      <div class="circle" style="left:0;top:150px;width:214px;height:236px;border-radius:50%;background:rgba(125,171,51,.95);padding-top:78px">
        <svg width="30" height="30" viewBox="0 0 30 30"><circle cx="15" cy="15" r="11" fill="none" stroke="#fff" stroke-width="2"/><circle cx="15" cy="15" r="5" fill="none" stroke="#fff" stroke-width="2"/></svg>
        <h4>Values</h4>
        <p>Lorem ipsum dolor sit<br>amet, con sectetur<br>adipiscing elita.</p>
      </div>
      <div class="circle" style="left:176px;top:150px;width:244px;height:244px;background:rgba(30,122,100,.92);padding-top:78px">
        <svg width="30" height="30" viewBox="0 0 30 30"><circle cx="15" cy="13" r="11" fill="none" stroke="#fff" stroke-width="2"/><circle cx="15" cy="10" r="3" fill="#fff"/><path d="M9 20c2-5 10-5 12 0" stroke="#fff" stroke-width="2" fill="none"/></svg>
        <h4>Spiritual Life</h4>
        <p>Lorem ipsum dolor sit<br>amet, con sectetur<br>adipiscing elita.</p>
      </div>
      <div class="circle" style="left:172px;top:176px;width:76px;height:76px;background:#fff;box-shadow:0 2px 8px rgba(0,0,0,.2)"></div>
    </div>
  </section>

  <!-- faq -->
  <section class="abs faq">
    <h2 class="abs">FAQ</h2>
  </section>
  <div class="abs faq-item" style="top:2967px">What makes this project unique?<span class="plus"><svg width="14" height="14" viewBox="0 0 14 14"><path d="M7 1v12M1 7h12" stroke="#fff" stroke-width="2.6"/></svg></span></div>
  <div class="abs faq-item" style="top:3036px">Does this project assume that the impact of religion is always positive?<span class="plus"><svg width="14" height="14" viewBox="0 0 14 14"><path d="M7 1v12M1 7h12" stroke="#fff" stroke-width="2.6"/></svg></span></div>
  <div class="abs faq-item" style="top:3104px">How can I collaborate?<span class="plus"><svg width="14" height="14" viewBox="0 0 14 14"><path d="M7 1v12M1 7h12" stroke="#fff" stroke-width="2.6"/></svg></span></div>
  <div class="abs faq-item" style="top:3173px">Will Harrowgate U faculty lead all projects?<span class="plus"><svg width="14" height="14" viewBox="0 0 14 14"><path d="M7 1v12M1 7h12" stroke="#fff" stroke-width="2.6"/></svg></span></div>

  <!-- footer -->
  <footer class="footer">
    <div class="abs footer-bg"></div>
    <svg class="abs" style="left:0;top:3300px" width="1200" height="200" viewBox="0 3300 1200 200" aria-hidden="true">
      <path d="M0 3392 C140 3350 300 3318 450 3326 C650 3336 760 3490 980 3478 C1090 3472 1160 3420 1200 3385 L1200 3500 L0 3500 Z" fill="#7dab33"/>
      <path d="M0 3410 C140 3372 300 3350 450 3356 C650 3366 760 3492 980 3486 C1090 3482 1160 3446 1200 3418 L1200 3500 L0 3500 Z" fill="#2a2a2a"/>
    </svg>
    <div class="abs brand"><span class="brand-mark"></span><span class="brand-name">Wellness, Meaning, and the Inner Journey<br>The Research Program</span></div>
    <nav class="abs footer-nav"><a href="#">Home</a><a href="#">People</a><a href="#">Projects</a><a href="#">FAQs</a><a href="#">Resources</a><a href="#">Contact</a></nav>
    <div class="abs contact">
      <span><svg width="18" height="18" viewBox="0 0 24 24"><path d="M6.6 10.8a15 15 0 0 0 6.6 6.6l2.2-2.2c.3-.3.7-.4 1-.2 1.1.4 2.3.6 3.6.6.6 0 1 .4 1 1V20c0 .6-.4 1-1 1A17 17 0 0 1 3 4c0-.6.4-1 1-1h3.5c.6 0 1 .4 1 1 0 1.3.2 2.5.6 3.6.1.3 0 .7-.2 1z" fill="#1e8a6e"/></svg>123-456-7890</span>
      <span>|</span>
      <span><svg width="20" height="16" viewBox="0 0 20 16"><rect x="0" y="0" width="20" height="16" rx="2" fill="#1e8a6e"/><path d="M1 2l9 7 9-7" stroke="#2a2a2a" stroke-width="1.6" fill="none"/></svg>info@wmij-program.org</span>
    </div>
    <div class="abs social" aria-label="Social links"><span></span><span></span><span></span><span></span></div>
    <div class="abs rule"></div>
    <p class="abs copyright">© 2021 <em>WMIJ</em>. All Rights Reserved</p>
  </footer>

</div>
</body>
</html>
```